New B2C website design to help dads be better dads

DadHarbor is a website to help dads be the “best dad you can be.”

We require our website to be designed into a PSD format, no coding necessary.

The general concept is a two-page design. The first page is the login page, the second page is the home page. Once at the home page, rather than navigating to and from different pages, the user will push and pull through different visual and functional layers of the hierarchy. In theory, this should add to the user experience by having a visual anchor of where they are (through layered pagination) as well as improving loading times since the new information should only be a delta in data load versus a brand new page load.

The general look-and-feel we are going for is clean, simple, minimal. This means that the winning design will show us a good eye for web-optimized typography, good use of white (negative) space, and good use of a visually pleasing grid.

We require a total of 6 page "views" plus the landing page. We note that many of the views are similar to one another.
Landing page
Milestone view
Task view
Content view, articles
Content view, products
Search view
What's new view

Please review all of the additional information provided as well as the attachments for examples.

We provide the following websites as good references for:

Typography:
http://example-kelvorn.com/journal/

Use of white space:
http://www.trenvaskit.com/
http://moldrefin.com/

Example for “scrolling” page concept as well as good balance of color, typography, and white space:
http://www.qorbitalmeet.eu/

Please contact us with questions so that we can guide your design effort.
Updates

Hello designers,

The following information is added to help guide the design process:

1.  For the text dialogue below the landing page, please assume the following word count:
"why are we making dad harbor?": 250 words
"who are we?" 200 words
"what's the deal with the penguin logo?" 300 words

For the social media links, please see http://www.gravelplumbs.com/
Notice the floating "social" bar that is always to the right.  This is the concept we are going for, please try to implement this as you see fit. 

Target Market(s)

Fathers of young children ages 0-6 years old.

Industry/Entity Type

Product

Font styles to use
Sans Serif

Requirements
Must have
• Clean lines, minimal design concept

Incorporation of our logo (see attached document)

Header content is static for all views after landing page, see example

This page WILL be responsive, please keep that in mind when designing
The timeline bar should be to the left, with the timeline bar’s “milestones” also being responsive.

Designer is free to suggest font types, but any fonts used must be royalty-free and web-optimized. We request a minimum number of font types as well as fonts that load relatively fast. We reinforce that visually appealing typography is a significant factor in the winning design choice.

While we are not expecting the winning design to include code, please keep in mind that the final implementation needs to be optimized for desktop, tablet, and mobile platforms.

If you are using stock photography that is not generated by you, please provide where/how we can obtain imagery, as well as price.

All custom graphics must be available in original formats; Photoshop/GIMP layered files for layout design, and vector formats for logos, icons and other graphical elements.

Please incorporate “Blue” into design elements as you see fit, as the RGB 67 74 169 Blue is the primary color used in our brand. The complement to this blue is 255 202 0, a brownish orange. Feel free to use this color as well, although please keep it to a lesser amount.

Background color is your choice, do not feel the need to use the grey.
Should not have
• Excessive graphical content such that it affects loading times

Excessive use of too many font types such that it affects loading times

```html
<!DOCTYPE html>
<html lang="en">
<head>
<meta charset="utf-8">
<title>DadHarbor — Sign In</title>
<link href="https://fonts.googleapis.com/css2?family=Montserrat:wght@300;400;500;600;700&display=swap" rel="stylesheet">
<style>
  :root {
    --brand-blue: #434aa9;
    --brand-blue-dark: #373d94;
    --text-dark: #222428;
    --text-body: #6b6d72;
    --field-bg: #f4f4f4;
    --field-border: #dcdcdc;
    --white: #ffffff;
    --sky-top: #a9cde0;
    --sky-mid: #a3c5dc;
    --sky-low: #8fb6d6;
    --sea: #1c6fa3;
  }
  * { margin: 0; padding: 0; box-sizing: border-box; }
  html, body { width: 857px; height: 1200px; overflow: hidden; background: var(--white); }
  body { position: relative; font-family: "Montserrat", Arial, sans-serif; color: var(--text-dark); }

  .site-header { position: absolute; left: 0; top: 0; width: 857px; height: 118px; }
  .brand { position: absolute; left: 130px; top: 92px; font-size: 14px; font-weight: 600; letter-spacing: 0.2px; color: var(--brand-blue); line-height: 1; }
  .login-form { position: absolute; left: 332px; top: 61px; }
  .field { position: absolute; top: 0; height: 28px; background: var(--field-bg); border: 1px solid var(--field-border); font: 400 7.5px "Montserrat", Arial, sans-serif; color: #777; padding: 0 7px; display: flex; align-items: center; }
  .field-username { left: 0; width: 152px; }
  .field-password { left: 166px; width: 141px; }
  .sign-in { position: absolute; left: 315px; top: 0; width: 79px; height: 28px; background: var(--brand-blue); border: 1px solid var(--brand-blue-dark); color: var(--white); font: 600 10.5px "Montserrat", Arial, sans-serif; display: flex; align-items: center; justify-content: center; }
  .login-links { position: absolute; top: 38px; left: 165px; font-size: 7.5px; color: var(--brand-blue); white-space: nowrap; }
  .login-links span { position: absolute; top: 0; }
  .login-links .forgot { left: 0; }
  .login-links .request { left: 83px; }

  .hero { position: absolute; left: 0; top: 118px; width: 857px; height: 541px; overflow: hidden; }
  .hero-photo { position: absolute; inset: 0; background: linear-gradient(180deg, var(--sky-top) 0%, var(--sky-mid) 55%, var(--sky-low) 88%, var(--sea) 94%, var(--sea) 100%); }
  .hero-title { position: absolute; left: 126px; top: 216px; font-size: 35px; font-weight: 500; line-height: 35px; color: var(--white); letter-spacing: 0.6px; }
  .hero-title .accent { color: var(--brand-blue); font-weight: 600; }
  .hero-cta { position: absolute; left: 309px; top: 500px; width: 238px; height: 41px; background: var(--brand-blue); color: var(--white); font-size: 10px; font-weight: 600; letter-spacing: 0.6px; display: flex; align-items: center; justify-content: center; }
  .cta-arrow { position: absolute; left: 418px; top: 650px; }

  .about { position: absolute; left: 130px; top: 0; width: 598px; }
  .about-title { position: absolute; top: 725px; font-size: 15.5px; font-weight: 700; color: var(--brand-blue); letter-spacing: 0.4px; white-space: nowrap; }
  .question { position: absolute; font-size: 11.5px; font-weight: 400; color: var(--text-dark); white-space: nowrap; }
  .answer { position: absolute; width: 598px; font-size: 8.6px; font-weight: 400; line-height: 19.2px; color: var(--text-body); }
  .q1 { top: 765px; } .a1 { top: 803px; }
  .q2 { top: 886px; } .a2 { top: 932px; }
  .q3 { top: 1015px; } .a3 { top: 1052px; }

  .site-footer { position: absolute; left: 0; top: 1150px; width: 857px; height: 50px; background: var(--brand-blue); color: var(--white); font-size: 8.5px; font-weight: 300; display: flex; align-items: center; justify-content: center; }
</style>
</head>
<body>
  <header class="site-header">
    <div class="brand">DADHARBOR</div>
    <div class="login-form">
      <div class="field field-username">Username</div>
      <div class="field field-password">Password</div>
      <div class="sign-in">Sign In</div>
      <div class="login-links">
        <span class="forgot">Forgot Login &nbsp;?</span>
        <span class="request">Request Access</span>
      </div>
    </div>
  </header>

  <section class="hero">
    <div class="hero-photo" role="img" aria-label="Photo of a smiling father lifting his young son, arms outstretched, against a clear blue sky and sea"></div>
    <h1 class="hero-title">Be the best<br><span class="accent">Dad</span> you can ?</h1>
    <div class="hero-cta">LEARN ABOUT DAD HARBOR</div>
  </section>
  <svg class="cta-arrow" width="20" height="18" viewBox="0 0 20 18" aria-hidden="true">
    <polygon points="0,0 20,0 10,18" fill="#434aa9"/>
    <polyline points="4,3 10,9 16,3" fill="none" stroke="#ffffff" stroke-width="2.2"/>
  </svg>

  <main class="about">
    <h2 class="about-title">ABOUT DAD HARBOR</h2>
    <h3 class="question q1">Why are we making Dad Harbor?</h3>
    <p class="answer a1">Lorem ipsum dolor sit amet, consectetur adipisicing elit, sed do eiusmod tempor incididunt ut labore et dolore magna aliqua. Ut enim ad minim veniam, quis nostrud exercitation ullamco laboris nisi ut aliquip ex ea commodo consequat. Duis aute irure dolor in reprehenderit in voluptate velit esse cillum dolore eu fugiat nulla pariatur. Excepteur sint ccaecat cupidatat non proident, sunt in culpa qui officia deserunt mollit anim id est laborum</p>
    <h3 class="question q2">Who are we?</h3>
    <p class="answer a2">Lorem ipsum dolor sit amet, consectetur adipisicing elit, sed do eiusmod tempor incididunt ut labore et dolore magna aliqua. Ut enim ad minim veniam, quis nostrud exercitation ullamco laboris nisi ut aliquip ex ea commodo consequat. Duis aute irure dolor in reprehenderit in voluptate velit esse cillum dolore eu fugiat nulla pariatur. Excepteur sint ccaecat cupidatat non proident, sunt in culpa qui officia deserunt mollit anim id est laborum</p>
    <h3 class="question q3">What’s the deal with the Penguin logo?</h3>
    <p class="answer a3">Lorem ipsum dolor sit amet, consectetur adipisicing elit, sed do eiusmod tempor incididunt ut labore et dolore magna aliqua. Ut enim ad minim veniam, quis nostrud exercitation ullamco laboris nisi ut aliquip ex ea commodo consequat. Duis aute irure dolor in reprehenderit in voluptate velit esse cillum dolore eu fugiat nulla pariatur. Excepteur sint ccaecat cupidatat non proident, sunt in culpa qui officia deserunt mollit anim id est laborum</p>
  </main>

  <footer class="site-footer">Copyright © 2013 &nbsp;Company Name | All Rights Reserved</footer>
</body>
</html>
```